Quiet Harbor Podcast W/ Dr. Lena Marsh

Podcast Cover Art. I am in search of a re-design for my existing podcast. We have over 100 episodes, but I want to change the name to Quiet Harbor Podcast With Dr. Lena Marsh. I'm open to any ideas, and have attached source file image to use. ( note: NO brain images please).

```html
<!DOCTYPE html>
<html lang="en">
<head>
<meta charset="UTF-8">
<title>Quiet Harbor Podcast With Dr. Lena Marsh</title>
<link href="https://fonts.googleapis.com/css2?family=Archivo+Black&family=Oswald:wght@500&family=Poppins:wght@500&display=swap" rel="stylesheet">
<style>
  :root {
    --bg-blush: #fbd5c8;
    --bg-blush-light: #fde0d5;
    --coral: #ff6b50;
    --brick: #c9452c;
    --brick-dark: #9e2f1c;
    --brown: #52360f;
    --skin: #e6b49d;
    --hair: #8f6a2a;
  }
  * { margin: 0; padding: 0; box-sizing: border-box; }
  html, body { width: 1200px; height: 1200px; overflow: hidden; background: var(--bg-blush); }
  .cover {
    position: relative;
    width: 1200px;
    height: 1200px;
    overflow: hidden;
    background: radial-gradient(circle at 25% 30%, var(--bg-blush-light), var(--bg-blush) 70%);
  }
  .cover-art { position: absolute; inset: 0; width: 1200px; height: 1200px; }
  .title {
    position: absolute;
    left: 92px;
    font-family: "Archivo Black", sans-serif;
    line-height: 1;
    text-transform: uppercase;
    letter-spacing: -2px;
  }
  .title-top { top: 100px; font-size: 224px; color: var(--coral); }
  .title-bottom { top: 306px; font-size: 175px; color: var(--brown); }
  .with {
    position: absolute;
    left: 100px;
    top: 752px;
    font-family: "Poppins", sans-serif;
    font-size: 40px;
    letter-spacing: 6px;
    color: var(--coral);
  }
  .host {
    position: absolute;
    left: 99px;
    top: 815px;
    font-family: "Oswald", sans-serif;
    font-weight: 500;
    font-size: 90px;
    line-height: 1;
    color: var(--brown);
    text-transform: uppercase;
    white-space: nowrap;
  }
  .label {
    position: absolute;
    left: 100px;
    top: 1042px;
    font-family: "Poppins", sans-serif;
    font-size: 28px;
    letter-spacing: 14px;
    color: var(--coral);
  }
</style>
</head>
<body>
<main class="cover">
  <svg class="cover-art" viewBox="0 0 1200 1200" xmlns="http://www.w3.org/2000/svg">
    <defs>
      <linearGradient id="ribbonFill" x1="0" y1="0" x2="1" y2="1">
        <stop offset="0" stop-color="var(--brick)"/>
        <stop offset="1" stop-color="var(--brick-dark)"/>
      </linearGradient>
      <linearGradient id="portraitFill" x1="0" y1="0" x2="0" y2="1">
        <stop offset="0" stop-color="var(--skin)"/>
        <stop offset="0.6" stop-color="var(--coral)"/>
        <stop offset="1" stop-color="var(--brick)"/>
      </linearGradient>
    </defs>
    <path class="ribbon" role="img" aria-label="Flowing marbled red ribbon"
      d="M760 0 H1200 V330 C1120 350 1070 380 1050 430 C1030 480 1020 530 1010 560 H960 C960 500 950 470 950 430 C950 330 930 200 870 110 C830 60 790 25 760 0 Z"
      fill="url(#ribbonFill)"/>
    <path class="portrait-area" role="img" aria-label="Illustrated portrait of the host in a coral checked blazer"
      d="M760 560 H1200 V1200 H720 V600 Q720 560 760 560 Z"
      fill="url(#portraitFill)"/>
  </svg>

  <h1 class="title title-top">Quiet</h1>
  <p class="title title-bottom">Harbor</p>
  <p class="with">With</p>
  <p class="host">Dr. Lena Marsh</p>
  <p class="label">PODCAST</p>
</main>
</body>
</html>
```